Boutique Store Selling Antiques and Unique Finds

I need a Web Page designed for my Store Called "Willow Lane". I would like a very classic, muted design that looks European when pulled up. I will be selling Antiques from all over the world and Unique finds that have reproduced. I will also be selling high-end purses and jewelry with unique, reasonable products for the every-day buyer as well.

Target Market(s)

25-70 year old men and women;)

Coding

Coded - Design and coding required

Number of Pages Required

1 page

Colors

Designer to choose only greyscale colors for use in the design.

Requirements
Must have
• I want it

```html
<!DOCTYPE html>
<html lang="en">
<head>
<meta charset="utf-8">
<title>Willow Lane — Antiques and Unique Finds</title>
<link rel="stylesheet" href="https://fonts.googleapis.com/css2?family=IBM+Plex+Sans:wght@400;500;600&family=Rubik:wght@500;700&display=swap">
<style>
:root{
  --ink:#1c1c1c;
  --text:#333;
  --muted:#555;
  --accent:#3a3a3a;
  --accent-light:#f2f2f2;
  --line:#d6d6d6;
  --rule:#a9a9a9;
  --tint:#f2f2f2;
  --white:#fff;
  --footer:#262626;
  --footer-text:#d9d9d9;
}
*{box-sizing:border-box;margin:0;padding:0}
html,body{width:1200px;height:3832px;overflow:hidden;background:var(--white)}
body{position:relative;font-family:"IBM Plex Sans",Arial,sans-serif;color:var(--text)}
.abs{position:absolute}
.brand{font-family:"IBM Plex Sans",Arial,sans-serif;font-weight:500;text-transform:uppercase;letter-spacing:5px;color:var(--ink);white-space:nowrap}

/* header */
.site-header{left:0;top:0;width:1200px;height:109px;background:var(--white)}
.site-header .brand{left:131px;top:52px;font-size:26px}
.search{left:781px;top:23px;width:225px;height:31px;border:1px solid #999;font-size:11px;padding:8px 12px;color:#555}
.search svg{position:absolute;right:10px;top:8px}
.cart{left:1028px;top:24px}
.cart-badge{left:1050px;top:22px;width:17px;height:17px;border-radius:50%;background:var(--accent);color:#fff;font-size:10px;text-align:center;line-height:17px}
.nav{left:496px;top:75px;font-size:14px;font-weight:500;color:var(--ink)}
.nav a{color:inherit;text-decoration:none;position:absolute;white-space:nowrap}
.nav a.active{color:var(--ink);font-weight:600;border-bottom:1.5px solid var(--ink);padding-bottom:1px}

/* hero */
.hero{left:0;top:109px;width:1200px;height:572px;background:linear-gradient(90deg,#dcdcdc 0%,#cbcbcb 40%,#6a6a6a 60%,#8e8e8e 80%,#c8c8c8 100%)}
.hero h1{left:127px;top:196px;font-family:Rubik,Arial,sans-serif;font-weight:700;font-size:34px;color:var(--ink);letter-spacing:.5px;white-space:nowrap}
.hero p{left:130px;top:250px;font-size:17px;line-height:24px;color:var(--ink);white-space:nowrap}
.btn{display:inline-block;background:var(--accent);color:#fff;font-family:Rubik,Arial,sans-serif;font-weight:700;text-transform:uppercase;text-align:center}
.hero .btn{left:132px;top:322px;width:150px;height:45px;line-height:45px;font-size:19px}
.dots{left:562px;top:534px;display:flex;gap:10px}
.dots i{width:6px;height:6px;border-radius:50%;background:#fff;display:block}
.dots i.on{background:var(--accent)}

/* section heads */
.sec-title{width:1200px;left:0;text-align:center;font-family:Rubik,Arial,sans-serif;font-weight:500;font-size:23px;color:var(--ink)}
.sec-rule{left:577px;width:45px;height:3px;background:var(--rule)}

/* product cards */
.card{width:223px;height:359px;border:1px solid var(--line);background:var(--white)}
.card .ph{width:100%;height:213px}
.card .name{position:absolute;left:21px;top:229px;font-size:14px;line-height:19px;color:var(--ink);white-space:nowrap}
.card .price{position:absolute;left:21px;top:281px;font-size:15px;font-weight:600;color:var(--ink)}
.card .btn-sm{position:absolute;left:21px;top:311px;width:100px;height:24px;line-height:24px;font-size:10.5px;background:var(--accent);color:#fff;font-family:Rubik,Arial,sans-serif;font-weight:700;text-align:center}
.chev{width:16px;height:26px}

/* arrivals */
.arrivals{left:0;top:1205px;width:1200px;height:745px;background:var(--tint)}
.arrival{width:461px;height:565px;border:1px solid #bdbdbd;background:var(--white);top:1325px}
.arrival .ph{width:100%;height:434px}
.arrival h3{position:absolute;top:463px;width:100%;text-align:center;font-family:Rubik,Arial,sans-serif;font-weight:500;font-size:19px;color:var(--ink)}
.arrival p{position:absolute;top:493px;width:100%;text-align:center;font-size:14px;color:var(--ink)}
.arrival .price{position:absolute;top:521px;width:100%;text-align:center;font-size:19px;font-weight:600;color:var(--ink)}
.arrival .btn-sm{position:absolute;left:186px;top:553px;width:88px;height:24px;line-height:24px;font-size:10.5px;background:var(--accent);color:#fff;font-family:Rubik,Arial,sans-serif;font-weight:700;text-align:center}

/* offer */
.offer{left:0;top:1950px;width:1200px;height:461px;background:linear-gradient(90deg,#2a2a2a 0%,#4a4a4a 25%,#252525 55%,#2e2e2e 100%)}
.offer h2{left:678px;top:68px;font-family:Rubik,Arial,sans-serif;font-weight:500;font-size:32px;color:#fff;letter-spacing:1px;white-space:nowrap}
.offer p{left:678px;top:120px;font-size:19px;line-height:26px;color:#e4e4e4;white-space:nowrap}
.offer .big{left:677px;top:196px;font-family:Rubik,Arial,sans-serif;font-weight:700;font-size:44px;color:#fff;letter-spacing:1px;white-space:nowrap}
.offer .btn{left:681px;top:289px;width:150px;height:45px;line-height:45px;font-size:19px;background:var(--accent-light);color:var(--ink)}

/* blog */
.post{width:297px;height:391px;border:1px solid #bdbdbd;background:var(--white);top:2528px}
.post .ph{width:100%;height:198px}
.post h4{position:absolute;left:25px;top:227px;font-size:13px;line-height:19px;font-weight:600;color:var(--ink);text-transform:uppercase;white-space:nowrap}
.post p{position:absolute;left:25px;top:274px;font-size:12px;line-height:18px;color:var(--muted);white-space:nowrap}
.post .btn-sm{position:absolute;left:27px;top:338px;width:87px;height:22px;line-height:22px;font-size:10.5px;background:var(--accent);color:#fff;font-family:Rubik,Arial,sans-serif;font-weight:700;text-align:center}

.featured{left:0;top:2974px;width:1200px;height:507px;background:var(--tint)}

/* footer */
.site-footer{left:0;top:3481px;width:1200px;height:351px;background:var(--footer);color:var(--footer-text)}
.site-footer .brand{left:131px;top:141px;font-size:26px;color:#fff}
.foot-head{font-size:13px;font-weight:600;color:#fff;letter-spacing:.5px}
.foot-list{font-size:11.5px;line-height:20px;color:var(--footer-text)}
.foot-item{font-size:11.5px;line-height:16px;white-space:nowrap}
.ico{width:22px;height:22px;border-radius:50%;background:#fff}
.foot-rule{left:130px;top:274px;width:940px;height:1px;background:#3b3b3b}
.copy{left:0;width:1200px;top:310px;text-align:center;font-size:10px;color:#cfcfcf}
</style>
</head>
<body>

<header class="abs site-header">
  <div class="abs brand">Willow Lane</div>
  <div class="abs search">SEARCH
    <svg width="11" height="11" viewBox="0 0 12 12"><circle cx="5" cy="5" r="3.8" fill="none" stroke="#666" stroke-width="1.3"/><path d="M8 8l3 3" stroke="#666" stroke-width="1.3"/></svg>
  </div>
  <svg class="abs cart" width="30" height="28" viewBox="0 0 30 28"><path d="M1 3h5l4 15h15l3-11H8" fill="none" stroke="#222" stroke-width="2"/><path d="M11 11h15M12 14h13" stroke="#222" stroke-width="1.5"/><circle cx="12" cy="23" r="2.3" fill="#222"/><circle cx="23" cy="23" r="2.3" fill="#222"/></svg>
  <div class="abs cart-badge">0</div>
  <nav class="abs nav">
    <a class="active" style="left:0">HOME</a>
    <a style="left:76px">ABOUT US</a>
    <a style="left:182px">PRODUCTS</a>
    <a style="left:290px">SHOP ONLINE</a>
    <a style="left:422px">BLOG</a>
    <a style="left:490px">CONTACT US</a>
  </nav>
</header>

<section class="abs hero">
  <div class="abs" role="img" aria-label="Ornate antique gilded crown on a dark pedestal" style="left:0;top:0;width:1200px;height:572px;background:linear-gradient(90deg,rgba(236,236,236,.85) 0%,rgba(225,225,225,.4) 35%,rgba(0,0,0,0) 55%)"></div>
  <h1 class="abs">CROWN ANTIQUES</h1>
  <p class="abs">Lorem Ipsum is simply dummy text of<br>the printing and typesetting.</p>
  <a class="abs btn">Shop Now</a>
  <div class="abs dots"><i></i><i></i><i class="on"></i><i></i><i></i></div>
</section>

<h2 class="abs sec-title" style="top:716px">OUR PRODUCTS</h2>
<div class="abs sec-rule" style="top:759px"></div>

<svg class="abs chev" style="left:78px;top:962px" viewBox="0 0 16 26"><path d="M13 2L3 13l10 11" fill="none" stroke="#999" stroke-width="2"/></svg>
<svg class="abs chev" style="left:1103px;top:962px" viewBox="0 0 16 26"><path d="M3 2l10 11L3 24" fill="none" stroke="#999" stroke-width="2"/></svg>

<div class="abs card" style="left:129px;top:796px">
  <div class="ph" role="img" aria-label="Gilded antique crown resting on old books" style="background:linear-gradient(180deg,#5e5e5e,#7a7a7a 60%,#3a3a3a)"></div>
  <div class="name">Lorem Ipsum is simply<br>dummy text</div><div class="price">$251.00</div><div class="btn-sm">ADD TO CART</div>
</div>
<div class="abs card" style="left:367px;top:796px">
  <div class="ph" role="img" aria-label="Antique brass hand mirror" style="background:linear-gradient(180deg,#efefef,#dedede)"></div>
  <div class="name">Lorem Ipsum is simply<br>dummy text</div><div class="price">$251.00</div><div class="btn-sm">ADD TO CART</div>
</div>
<div class="abs card" style="left:607px;top:796px">
  <div class="ph" role="img" aria-label="Vintage rotary telephone on a stand" style="background:linear-gradient(180deg,#8f8f8f,#b5b5b5 60%,#444)"></div>
  <div class="name">Lorem Ipsum is simply<br>dummy text</div><div class="price">$251.00</div><div class="btn-sm">ADD TO CART</div>
</div>
<div class="abs card" style="left:846px;top:796px">
  <div class="ph" role="img" aria-label="Antique wooden chair with upholstered seat" style="background:linear-gradient(180deg,#c4c4c4,#8c8c8c 70%,#5a5a5a)"></div>
  <div class="name">Lorem Ipsum is simply<br>dummy text</div><div class="price">$251.00</div><div class="btn-sm">ADD TO CART</div>
</div>

<section class="abs arrivals"></section>
<h2 class="abs sec-title" style="top:1243px">NEW ARRIVALS</h2>
<div class="abs sec-rule" style="top:1285px"></div>

<div class="abs arrival" style="left:129px">
  <div class="ph" role="img" aria-label="Wicker handbag on a checked picnic blanket" style="background:linear-gradient(180deg,#6e6e6e 0%,#7c7c7c 45%,#8f8f8f 75%,#4a4a4a)"></div>
  <h3>PURSES</h3><p>Lorem Ipsum is simply dummy text</p><div class="price">$145.00</div><div class="btn-sm">SHOP NOW</div>
</div>
<div class="abs arrival" style="left:607px">
  <div class="ph" role="img" aria-label="Gold jewelry with sparkling stones" style="background:radial-gradient(circle at 50% 55%,#9e9e9e,#c9c9c9 50%,#e6e6e6)"></div>
  <h3>JEWELRY</h3><p>Lorem Ipsum is simply dummy text</p><div class="price">$145.00</div><div class="btn-sm">SHOP NOW</div>
</div>

<section class="abs offer">
  <div class="abs" role="img" aria-label="Antique brass mantel clock on a wooden table" style="left:90px;top:20px;width:300px;height:420px;background:radial-gradient(ellipse at 50% 50%,#777,rgba(42,42,42,0) 70%)"></div>
  <h2 class="abs">SPECIAL OFFERS</h2>
  <p class="abs">Contrary to popular belief, Lorem Ipsum is not<br>simply random text. It has roots in a piece.</p>
  <div class="abs big">GET 50% OFF</div>
  <a class="abs btn">Shop Now</a>
</section>

<h2 class="abs sec-title" style="top:2450px">LATEST BLOG</h2>
<div class="abs sec-rule" style="top:2491px"></div>

<article class="abs post" style="left:132px">
  <div class="ph" role="img" aria-label="Antique shop interior with a wooden cabinet and porcelain" style="background:linear-gradient(180deg,#2e2e2e,#6a6a6a 50%,#5a5a5a)"></div>
  <h4>Contrary to popular belief<br>Lorem Ipsum is not simply</h4>
  <p>There are many variations of passages of<br>Lorem Ipsum available, but the majority<br>have suffered alteration in some</p>
  <div class="btn-sm">READ MORE</div>
</article>
<article class="abs post" style="left:452px">
  <div class="ph" role="img" aria-label="Vintage tufted armchair against a pale wall" style="background:linear-gradient(180deg,#e4e4e4,#d2d2d2 75%,#c2c2c2)"></div>
  <h4>Contrary to popular belief<br>Lorem Ipsum is not simply</h4>
  <p>There are many variations of passages of<br>Lorem Ipsum available, but the majority<br>have suffered alteration in some</p>
  <div class="btn-sm">READ MORE</div>
</article>
<article class="abs post" style="left:772px">
  <div class="ph" role="img" aria-label="Old book with a quill pen and inkwell" style="background:linear-gradient(180deg,#1e1e1e,#5e5e5e 55%,#2e2e2e)"></div>
  <h4>Contrary to popular belief<br>Lorem Ipsum is not simply</h4>
  <p>There are many variations of passages of<br>Lorem Ipsum available, but the majority<br>have suffered alteration in some</p>
  <div class="btn-sm">READ MORE</div>
</article>

<section class="abs featured"></section>
<h2 class="abs sec-title" style="top:3007px">FEATURED PRODUCTS</h2>
<div class="abs sec-rule" style="top:3048px"></div>

<svg class="abs chev" style="left:78px;top:3252px" viewBox="0 0 16 26"><path d="M13 2L3 13l10 11" fill="none" stroke="#999" stroke-width="2"/></svg>
<svg class="abs chev" style="left:1103px;top:3252px" viewBox="0 0 16 26"><path d="M3 2l10 11L3 24" fill="none" stroke="#999" stroke-width="2"/></svg>

<div class="abs card" style="left:129px;top:3086px">
  <div class="ph" role="img" aria-label="Antique pocket watch" style="background:radial-gradient(circle at 50% 55%,#2e2e2e,#666 70%,#8a8a8a)"></div>
  <div class="name">Lorem Ipsum is simply<br>dummy text</div><div class="price">$251.00</div><div class="btn-sm">ADD TO CART</div>
</div>
<div class="abs card" style="left:367px;top:3086px">
  <div class="ph" role="img" aria-label="Ornate gilded mantel clock" style="background:linear-gradient(180deg,#eeeeee,#b4b4b4 60%,#9a9a9a)"></div>
  <div class="name">Lorem Ipsum is simply<br>dummy text</div><div class="price">$251.00</div><div class="btn-sm">ADD TO CART</div>
</div>
<div class="abs card" style="left:607px;top:3086px">
  <div class="ph" role="img" aria-label="Vintage gramophone with a large horn" style="background:linear-gradient(180deg,#d0d0d0,#8e8e8e 45%,#4a4a4a 85%)"></div>
  <div class="name">Lorem Ipsum is simply<br>dummy text</div><div class="price">$251.00</div><div class="btn-sm">ADD TO CART</div>
</div>
<div class="abs card" style="left:846px;top:3086px">
  <div class="ph" role="img" aria-label="Porcelain vase and plate" style="background:linear-gradient(180deg,#1c1c1c,#555 60%,#2a2a2a)"></div>
  <div class="name">Lorem Ipsum is simply<br>dummy text</div><div class="price">$251.00</div><div class="btn-sm">ADD TO CART</div>
</div>

<footer class="abs site-footer">
  <div class="abs brand">Willow Lane</div>

  <div class="abs foot-head" style="left:489px;top:52px">MENU</div>
  <div class="abs foot-list" style="left:489px;top:86px">HOME<br>ABOUT US<br>PRODUCTS<br>SHOP ONLINE<br>BLOG<br>CONTACT US</div>

  <div class="abs foot-head" style="left:680px;top:52px">CONTACT US</div>
  <svg class="abs" style="left:678px;top:88px" width="22" height="22" viewBox="0 0 22 22"><circle cx="11" cy="11" r="11" fill="#fff"/><path d="M11 5a4 4 0 0 0-4 4c0 3 4 8 4 8s4-5 4-8a4 4 0 0 0-4-4z" fill="#262626"/><circle cx="11" cy="9" r="1.4" fill="#fff"/></svg>
  <div class="abs foot-item" style="left:711px;top:88px">2750 Alder Row<br>Fernvale, OR 97002</div>
  <svg class="abs" style="left:678px;top:138px" width="22" height="22" viewBox="0 0 22 22"><circle cx="11" cy="11" r="11" fill="#fff"/><path d="M7 6c1-1 2-1 2.5 0l1 2c.3.6 0 1-.5 1.5-.3.3 0 1 1 2s1.7 1.3 2 1c.5-.5.9-.8 1.5-.5l2 1c1 .5 1 1.5 0 2.5-2 2-9-5-9.5-9.5z" fill="#262626"/></svg>
  <div class="abs foot-item" style="left:711px;top:138px">Call Us<br>555.014.2290</div>
  <svg class="abs" style="left:678px;top:188px" width="22" height="22" viewBox="0 0 22 22"><circle cx="11" cy="11" r="11" fill="#fff"/><rect x="5.5" y="7" width="11" height="8" fill="#262626"/><path d="M5.5 7l5.5 4.5L16.5 7" fill="none" stroke="#fff" stroke-width="1.1"/></svg>
  <div class="abs foot-item" style="left:711px;top:188px">E mail Us<br>info@WillowLane.com</div>

  <div class="abs foot-head" style="left:949px;top:52px">FOLLOW US</div>
  <div class="abs ico" style="left:948px;top:88px"></div>
  <div class="abs foot-item" style="left:983px;top:88px">Like us on<br>PAGEHUB</div>
  <div class="abs ico" style="left:948px;top:139px"></div>
  <div class="abs foot-item" style="left:983px;top:139px">Follow us on<br>CHIRPLINE</div>
  <div class="abs ico" style="left:948px;top:190px"></div>
  <div class="abs foot-item" style="left:983px;top:190px">Follow us on<br>WORKLINK</div>

  <div class="abs foot-rule"></div>
  <div class="abs copy">Copyright © 2021 All Rights Reserved</div>
</footer>

</body>
</html>
```